Varentoria Business Card and Letter Head

We are a leadership assessment consultancy based in Sydney, Australia. We help executive-level decison-makers select leaders for more senior level roles in corporate and government organisations. Our methodology is based on the latest research from the field of neuroscience.
We need a business card design and matching letter head that presents our company, Varentoria, as a:
1. trusted adviser to senior executive-level decison makers
2. niche consultancy who are experts in the field of assessing leadership talent
3. results-focused solution provider who balance scientific methods with pragmatic solutions
The following company details should be used in all designs:
Company Name: Varentoria
Details (for business card):
Derek Hanford
Prime Capacity Officer
Level 29, Marlow Tower
7 Marlow Square
Sydney, NSW 2000 Australia
Phone: 1300 582 714
Mobile: 0412 637 258
Email: derek.hanford@varentoria-example.com.au
Website: varentoria-example.com.au
I have attached the logo for Varentoria (for both a white and black background) - your business card and letter head designs must incoporate this logo and colour scheme.
Thanks for your interest in this project, I'm looking forward to receiving your ideas.
Regards,
Derek
Target Market(s)
Executive-level decison-makers in corporate and government organisations (e.g., CEO, VP, Head of Human Resources)
Industry/Entity Type
Leadership
Look and feel

```html
<!DOCTYPE html>
<html lang="en">
<head>
<meta charset="utf-8">
<title>Varentoria Business Card</title>
<link rel="stylesheet" href="https://fonts.googleapis.com/css2?family=Open+Sans:wght@400;700&family=Roboto:wght@500&family=Roboto+Condensed:wght@400&display=swap">
<style>
  :root {
    --backdrop: #efece7;
    --card: #ffffff;
    --ink-dark: #414141;
    --ink-text: #3c3c3c;
    --accent-red: #c0312b;
    --card-shadow: rgba(0, 0, 0, 0.22);
  }
  * { margin: 0; padding: 0; box-sizing: border-box; }
  html, body { width: 1200px; height: 469px; overflow: hidden; }
  body { background: var(--backdrop); position: relative; font-family: "Roboto Condensed", Arial, sans-serif; }

  .card {
    position: absolute;
    top: 87px;
    width: 524px;
    height: 294px;
    background: var(--card);
    box-shadow: 2px 3px 6px var(--card-shadow);
  }
  .card--front { left: 47px; }
  .card--back { left: 617px; }

  .edge-band { position: absolute; right: 0; width: 7px; }
  .edge-band--dark { top: 0; height: 133px; background: var(--ink-dark); }
  .edge-band--red { top: 141px; bottom: 0; background: var(--accent-red); }

  .brand { position: absolute; display: flex; align-items: center; gap: 12px; }
  .brand__square { width: 40px; height: 40px; background: var(--ink-dark); }
  .brand__name {
    font-family: "Roboto", Arial, sans-serif;
    font-weight: 500;
    font-size: 31px;
    color: var(--ink-dark);
    letter-spacing: -0.5px;
  }
  .card--front .brand { left: 46px; top: 53px; }
  .card--back .brand { left: 142px; top: 96px; }

  .contact-list {
    position: absolute;
    right: 233px;
    top: 146px;
    list-style: none;
    text-align: right;
    font-size: 12.5px;
    line-height: 18.5px;
    color: var(--ink-text);
  }
  .contact-list li { display: flex; justify-content: flex-end; align-items: center; gap: 6px; }
  .contact-list svg { width: 10px; height: 10px; fill: var(--ink-text); }

  .address {
    position: absolute;
    right: 233px;
    top: 234px;
    text-align: right;
    font-size: 12.5px;
    line-height: 18.5px;
    color: var(--ink-text);
    font-style: normal;
  }

  .person { position: absolute; left: 340px; top: 233px; width: 138px; text-align: center; font-family: "Open Sans", Arial, sans-serif; }
  .person__name { font-weight: 700; font-size: 14.5px; color: var(--accent-red); line-height: 18px; }
  .person__role { font-size: 11px; color: #222; line-height: 14px; }

  .website {
    position: absolute;
    left: 0;
    right: 7px;
    top: 166px;
    text-align: center;
    font-family: "Open Sans", Arial, sans-serif;
    font-size: 13px;
    color: var(--ink-text);
  }
  .website__domain { color: var(--accent-red); }
</style>
</head>
<body>
  <section class="card card--front" aria-label="Business card front">
    <div class="brand">
      <span class="brand__square"></span>
      <span class="brand__name">Varentoria</span>
    </div>

    <ul class="contact-list">
      <li><svg viewBox="0 0 10 10" aria-hidden="true"><path d="M2 0.5 L3.6 2.6 L2.7 3.6 C3.4 5 4.8 6.5 6.3 7.3 L7.4 6.4 L9.5 8 L8.3 9.5 C4.5 9.2 0.8 5.5 0.5 1.7 Z"/></svg>1300 582 714</li>
      <li><svg viewBox="0 0 10 10" aria-hidden="true"><path d="M2.5 0 H7.5 V10 H2.5 Z M3.3 1.2 V7.5 H6.7 V1.2 Z"/></svg>0412 637 258</li>
      <li><svg viewBox="0 0 10 10" aria-hidden="true"><path d="M0 2 H10 V8.5 H0 Z M0.8 2.6 L5 5.8 L9.2 2.6 Z" fill-rule="evenodd"/></svg>derek.hanford@varentoria-example.com.au</li>
      <li><svg viewBox="0 0 10 10" aria-hidden="true"><circle cx="5" cy="5" r="4.8"/></svg>www.varentoria-example.com.au</li>
    </ul>

    <address class="address">
      Level 29, Marlow Tower 7 Marlow Square<br>
      Sydney, NSW 2000 Australia
    </address>

    <div class="person">
      <p class="person__name">Derek Hanford</p>
      <p class="person__role">Prime Capacity Officer</p>
    </div>

    <span class="edge-band edge-band--dark"></span>
    <span class="edge-band edge-band--red"></span>
  </section>

  <section class="card card--back" aria-label="Business card back">
    <div class="brand">
      <span class="brand__square"></span>
      <span class="brand__name">Varentoria</span>
    </div>
    <p class="website">www.<span class="website__domain">varentoria-example</span>.com.au</p>

    <span class="edge-band edge-band--dark"></span>
    <span class="edge-band edge-band--red" style="top:143px"></span>
  </section>
</body>
</html>
```